Heating and Cooling Company mobile website

We need a website specifically designed for a viewing on a mobile device.

We serve the northern New Jersey heating, cooling and electrical residential market.

The goal is the drive traffic to the site by using Brintel Pay Per click. People will be searching for an HVAC contractor, and they land on our page. They need to get key info quickly without all the clutter of a desktop type of site.

Target Market(s)

Homeowners

Industry/Entity Type

Hvac

Coding

Coded - Design and coding required

Number of Pages Required

5+ page

Font styles to use
Serif

Requirements
Must have
• View attachments to see samples of the desktop version. It must have a similar color scheme
• The copy of the website is also attached
Nice to have
• Would like it to have a sort of Vardok feel to it. Make it seem like its an app that people are using and that its exciting to be on the website. It would be nice to have a page where customers can book appointments

```html
<!DOCTYPE html>
<html lang="en">
<head>
<meta charset="utf-8">
<title>Hearthline Climate – Mobile Home</title>
<link rel="stylesheet" href="https://fonts.googleapis.com/css2?family=Cinzel:wght@400;600;700&family=Libre+Baskerville:wght@400;700&family=Open+Sans:wght@400;600&display=swap">
<style>
:root{
  --red:#8e1b25;
  --red-bright:#d43f2a;
  --navy:#1d2242;
  --navy-2:#2d3560;
  --beige:#ecdfd1;
  --maroon:#4c0e19;
  --ink:#2a2d44;
  --grey:#6f6f74;
  --white:#ffffff;
}
*{box-sizing:border-box;margin:0;padding:0}
html,body{width:1200px;height:3830px;overflow:hidden;background:var(--white)}
body{font-family:"Open Sans",sans-serif;color:var(--ink)}
.page{position:relative;width:1200px;height:3830px}
section,header,footer{position:relative;width:1200px;overflow:hidden}

/* Header */
.site-header{height:118px;background:linear-gradient(#ffffff,#f1f1f3);border-bottom:2px solid #dcdcdf}
.phone{position:absolute;left:40px;top:40px;display:flex;align-items:center;gap:14px;font-weight:600;font-size:34px;color:var(--red)}
.brand{position:absolute;left:50%;top:22px;transform:translateX(-50%);font-family:"Cinzel",serif;font-weight:700;font-size:40px;line-height:1.05;color:var(--red);text-align:center;letter-spacing:1px}
.menu{position:absolute;right:44px;top:38px;width:80px}
.menu span{display:block;height:7px;background:#555;margin-bottom:12px;border-radius:2px}

/* Hero */
.hero{height:563px;background:#f7f5f3}
.hero-photo{position:absolute;left:380px;top:0;width:820px;height:563px;background:radial-gradient(ellipse at 55% 45%,#f0d3bf 0%,#e6cbb9 30%,#f3efec 65%,#fafafa 100%)}
.hero-copy{position:absolute;left:70px;top:170px;font-family:"Libre Baskerville",serif;text-transform:uppercase}
.hero-copy .small{font-size:50px;color:var(--red);line-height:1.1}
.hero-copy .big{font-size:74px;color:var(--navy);line-height:1.12}
.dots{position:absolute;left:78px;top:485px;display:flex;gap:14px}
.dots i{width:20px;height:20px;border-radius:50%;background:#2b2b2b}
.dots i.off{background:transparent;border:3px solid #2b2b2b}

/* Intro */
.intro{height:611px;text-align:center;padding-top:82px}
.intro h1{font-family:"Libre Baskerville",serif;font-weight:400;font-size:60px;color:var(--navy);letter-spacing:1px}
.intro h2{font-family:"Libre Baskerville",serif;font-weight:400;font-size:42px;color:var(--red);margin-top:14px}
.intro p{font-size:27px;line-height:1.55;color:var(--grey);width:980px;margin:34px auto 0}
.ribbon{position:relative;display:inline-block;margin-top:60px}
.ribbon svg{display:block}
.ribbon span{position:absolute;inset:0;display:flex;align-items:center;justify-content:center;font-size:31px;color:var(--white);font-weight:600;letter-spacing:1px}

/* Services */
.services{height:698px;background:var(--white)}
.services-band{position:absolute;left:0;top:0;width:1200px;height:100px;background:var(--beige)}
.services-title{position:absolute;left:0;top:28px;width:1200px;text-align:center;font-family:"Libre Baskerville",serif;font-size:46px;color:var(--red);z-index:2}
.services svg.shape{position:absolute;left:0;top:0}
.service{position:absolute;top:195px;width:340px;text-align:center}
.service.heating{left:145px}
.service.cooling{left:715px}
.service .label{margin-top:44px;color:var(--white);font-size:33px;font-weight:600;letter-spacing:1px}
.arrow{position:absolute;top:305px}
.arrow.left{left:40px}
.arrow.right{right:40px}

/* Video */
.video{height:675px;text-align:center}
.video-title{position:absolute;top:50px;left:0;width:1200px;display:flex;justify-content:center;align-items:center;gap:22px;font-family:"Libre Baskerville",serif;font-size:46px;color:var(--navy)}
.video-title .rule{display:flex;align-items:center}
.video-title .rule b{width:120px;height:3px;background:var(--red-bright)}
.video-title .rule i{width:18px;height:18px;border-radius:50%;background:var(--red-bright)}
.video-frame{position:absolute;left:55px;top:160px;width:1090px;height:490px;border:4px solid #dedede;background:#fff;padding:14px}
.video-still{position:relative;width:100%;height:100%;background:linear-gradient(90deg,#3c4a2e 0%,#5a6a52 22%,#9b8fe6 42%,#b7a7f0 70%,#cdbdf3 100%)}
.video-caption{position:absolute;left:430px;top:50px;text-align:center;width:560px}
.video-caption .lead{font-size:42px;color:#e2412e;line-height:1.2}
.video-caption .sub{font-size:44px;color:#2e2a3c;line-height:1.2;margin-top:60px;padding-left:70px}
.play{position:absolute;left:440px;top:185px;width:130px;height:130px;border-radius:50%;background:var(--white);display:flex;align-items:center;justify-content:center}

/* Residential / Commercial */
.sectors{height:827px}
.sectors-bg{position:absolute;inset:0;background:linear-gradient(180deg,#efe1d2 0%,#f2e4d6 45%,#ead8c8 100%)}
.sector{position:absolute;top:50px;width:520px;text-align:center}
.sector.residential{left:60px}
.sector.commercial{left:620px}
.sector .photo{width:340px;height:340px;border-radius:50%;margin:0 auto;border:12px solid var(--red-bright)}
.sector.commercial .photo{border-color:var(--red)}
.residential .photo{background:radial-gradient(circle at 45% 45%,#c9d3de,#7a8ea6 60%,#4e6078)}
.commercial .photo{background:radial-gradient(circle at 50% 40%,#e9d9b8,#b7b3ad 55%,#6e7178)}
.sector h3{margin-top:42px;font-size:33px;font-weight:600;color:var(--red-bright);text-transform:uppercase}
.sector.commercial h3{color:var(--red)}
.sector p{font-size:25px;line-height:1.45;color:#55545a;margin-top:14px}
.sector .ribbon{margin-top:46px}
.sector .ribbon span{font-size:25px}

/* Footer */
.site-footer{height:338px;background:var(--maroon);text-align:center}
.footer-top{height:80px;background:#f0e3d6;position:relative}
.footer-top::after{content:"";position:absolute;left:0;bottom:0;width:1200px;height:14px;background:#2a2440}
.footer-brand{position:absolute;left:50%;top:18px;transform:translateX(-50%);font-family:"Cinzel",serif;font-weight:700;font-size:30px;line-height:1.05;color:var(--red);background:#f0e3d6;padding:4px 20px;z-index:2}
.footer-nav{display:flex;justify-content:center;gap:38px;margin-top:36px;font-size:29px;color:var(--white)}
.copyright{margin-top:20px;font-size:22px;color:#b38c92}
.social{display:flex;justify-content:center;gap:22px;margin-top:34px}
.social i{width:56px;height:56px;border-radius:50%;border:3px solid var(--white)}
</style>
</head>
<body>
<div class="page">

  <header class="site-header">
    <div class="phone">
      <svg width="34" height="34" viewBox="0 0 24 24" aria-hidden="true"><path fill="#d8632a" d="M6.6 10.8a15 15 0 0 0 6.6 6.6l2.2-2.2c.3-.3.7-.4 1-.2 1.1.4 2.3.6 3.6.6.6 0 1 .4 1 1V20c0 .6-.4 1-1 1A17 17 0 0 1 3 4c0-.6.4-1 1-1h3.5c.6 0 1 .4 1 1 0 1.3.2 2.5.6 3.6.1.3 0 .7-.2 1z"/></svg>
      (555) 214-7780
    </div>
    <div class="brand">Hearthline<br>Climate</div>
    <div class="menu"><span></span><span></span><span></span></div>
  </header>

  <section class="hero">
    <div class="hero-photo" role="img" aria-label="Photo of a happy family of three laughing together at home"></div>
    <div class="hero-copy">
      <div class="small">We care of</div>
      <div class="big">Your<br>Feelings</div>
    </div>
    <div class="dots"><i class="off"></i><i></i><i></i><i></i></div>
  </section>

  <section class="intro">
    <h1>HEARTHLINE CLIMATE</h1>
    <h2>Most Trusted Heating &amp; Cooling Company</h2>
    <p>Integer congue augue et malesuada iaculis ipsum dui aliquet felis at cursus magna nisl nec elit Praesent elementum elit at tellus nec ultricies sit amet porttitor mattis enim in massa</p>
    <a class="ribbon">
      <svg width="390" height="100" viewBox="0 0 390 100"><polygon points="0,0 390,0 366,50 390,100 0,100 24,50" fill="var(--red-bright)"/><polygon points="14,10 376,10 356,50 376,90 14,90 34,50" fill="var(--red)"/></svg>
      <span>LEARN MORE</span>
    </a>
  </section>

  <section class="services">
    <div class="services-band"></div>
    <div class="services-title">OUR SERVICES</div>
    <svg class="shape" width="1200" height="698" viewBox="0 0 1200 698" aria-hidden="true">
      <defs><linearGradient id="navyFade" x1="0" y1="0" x2="0" y2="1"><stop offset="0" stop-color="#141830"/><stop offset="1" stop-color="#343c66"/></linearGradient></defs>
      <path d="M0 100 H520 Q600 100 600 170 Q600 100 680 100 H1200 V650 Q600 520 0 650 Z" fill="url(#navyFade)"/>
    </svg>
    <div class="service heating">
      <svg width="340" height="300" viewBox="0 0 340 300" aria-hidden="true">
        <ellipse cx="170" cy="290" rx="140" ry="10" fill="#0c0f20" opacity=".6"/>
        <path d="M40 30 Q170 -10 300 30 Q340 150 300 270 Q170 310 40 270 Q0 150 40 30Z" fill="var(--red-bright)"/>
        <path d="M55 44 Q170 10 285 44 Q320 150 285 256 Q170 290 55 256 Q20 150 55 44Z" fill="var(--red)"/>
        <g fill="none" stroke="#fff" stroke-width="7">
          <rect x="105" y="95" width="130" height="95" rx="6"/>
          <line x1="105" y1="118" x2="235" y2="118"/>
          <path d="M125 100v14M140 100v14M155 100v14M170 100v14M185 100v14M200 100v14M215 100v14"/>
          <line x1="120" y1="190" x2="120" y2="210"/><line x1="220" y1="190" x2="220" y2="210"/>
        </g>
      </svg>
      <div class="label">HEATING</div>
    </div>
    <div class="service cooling">
      <svg width="340" height="300" viewBox="0 0 340 300" aria-hidden="true">
        <ellipse cx="170" cy="290" rx="140" ry="10" fill="#0c0f20" opacity=".6"/>
        <path d="M40 30 Q170 -10 300 30 Q340 150 300 270 Q170 310 40 270 Q0 150 40 30Z" fill="var(--red-bright)"/>
        <path d="M55 44 Q170 10 285 44 Q320 150 285 256 Q170 290 55 256 Q20 150 55 44Z" fill="var(--red)"/>
        <g fill="none" stroke="#fff" stroke-width="7">
          <rect x="95" y="95" width="150" height="70" rx="10"/>
          <line x1="115" y1="145" x2="225" y2="145"/>
          <path d="M135 180v26M155 180v32M170 180v34M185 180v32M205 180v26"/>
        </g>
      </svg>
      <div class="label">AIR CONDITIONING</div>
    </div>
    <svg class="arrow left" width="30" height="50" viewBox="0 0 30 50" aria-hidden="true"><polyline points="24,4 6,25 24,46" fill="none" stroke="#fff" stroke-width="6"/></svg>
    <svg class="arrow right" width="30" height="50" viewBox="0 0 30 50" aria-hidden="true"><polyline points="6,4 24,25 6,46" fill="none" stroke="#fff" stroke-width="6"/></svg>
  </section>

  <section class="video">
    <div class="video-title">
      <span class="rule"><b></b><i></i></span>
      WATCH OUR VIDEO
      <span class="rule"><i></i><b></b></span>
    </div>
    <div class="video-frame">
      <div class="video-still" role="img" aria-label="Video still of a technician reading a clipboard beside the title card">
        <div class="video-caption">
          <div class="lead">When searching for the<br>Right HVAC Contractor</div>
          <div class="sub">Keep these<br>important things<br>in mind</div>
        </div>
        <div class="play"><svg width="54" height="60" viewBox="0 0 54 60" aria-hidden="true"><polygon points="8,0 54,30 8,60" fill="#111"/></svg></div>
      </div>
    </div>
  </section>

  <section class="sectors">
    <div class="sectors-bg" role="img" aria-label="Soft blurred photo of a family at the beach"></div>
    <div class="sector residential">
      <div class="photo" role="img" aria-label="Photo of a technician servicing an indoor air conditioning unit"></div>
      <h3>Residential Services</h3>
      <p>iaculis ipsum dui aliquet felis at<br>cursus magna nisl nec elit<br>Praesent elementum</p>
      <a class="ribbon">
        <svg width="280" height="72" viewBox="0 0 280 72"><polygon points="0,0 280,0 262,36 280,72 0,72 18,36" fill="var(--red-bright)"/><polygon points="10,8 270,8 254,36 270,64 10,64 26,36" fill="var(--red)"/></svg>
        <span>LEARN MORE</span>
      </a>
    </div>
    <div class="sector commercial">
      <div class="photo" role="img" aria-label="Photo of rooftop commercial condenser units at sunset"></div>
      <h3>Commercial Services</h3>
      <p>iaculis ipsum dui aliquet felis at<br>cursus magna nisl nec elit<br>Praesent elementum</p>
      <a class="ribbon">
        <svg width="280" height="72" viewBox="0 0 280 72"><polygon points="0,0 280,0 262,36 280,72 0,72 18,36" fill="var(--red-bright)"/><polygon points="10,8 270,8 254,36 270,64 10,64 26,36" fill="var(--red)"/></svg>
        <span>LEARN MORE</span>
      </a>
    </div>
  </section>

  <footer class="site-footer">
    <div class="footer-top"><div class="footer-brand">Hearthline<br>Climate</div></div>
    <nav class="footer-nav"><span>Home</span><span>About</span><span>Services</span><span>Blog</span><span>Testimonial</span><span>Contact</span></nav>
    <div class="copyright">© 2017 Company Name  All right reserved</div>
    <div class="social"><i></i><i></i><i></i><i></i></div>
  </footer>

</div>
</body>
</html>
```